Beautiful design for wordpress

I need a beautiful, colourful and feminine website. My business is called 'The Velvet Lantern', and I sell crystals, books, CD's, pendulums and other metaphysical items. I also provide Reiki (energy healing).
I want this design to be eye catching and inspire happiness and joy in those who see it. And I would love to see the use of the logo and its colours :)
Please add these on the web design: Home, About, Online store, Blog

Industry/Entity Type

Business

Requirements
Must have
• Colourful and playful, must use the logo somewhere, have the words on a menu saying 'Home, Blog, Online store and about' (or similar to those)And the design must stand out!
Should not have
• grey, brown and other boring colours.

```html
<!DOCTYPE html>
<html lang="en">
<head>
<meta charset="utf-8">
<title>The Velvet Lantern – Crystals, Books & Reiki</title>
<link rel="stylesheet" href="https://fonts.googleapis.com/css2?family=Open+Sans:wght@300;400;600;700&display=swap">
<style>
:root{
  --coral:#f47a6e;
  --coral-dark:#e9645a;
  --pink:#e8457d;
  --orange:#f7941d;
  --footer:#f8a232;
  --footer-dark:#e98c17;
  --green:#9cc63b;
  --green-dark:#84b02a;
  --ink:#444a52;
  --muted:#6b7078;
  --line:#e4e4e4;
  --hero-bg:#f2f3f5;
  --page:#ffffff;
  --outer:#f6f4f7;
}
*{box-sizing:border-box;margin:0;padding:0}
html,body{width:896px;height:1200px;overflow:hidden}
body{font-family:"Open Sans",Arial,sans-serif;color:var(--ink);background:var(--outer)}
.page{position:relative;width:896px;height:1200px;background:var(--page);overflow:hidden}
.wrap{position:absolute;left:44px;width:808px}

/* header */
.site-header{top:0;height:80px}
.brand{position:absolute;left:0;top:14px;display:flex;align-items:center;gap:8px}
.brand-dot{width:34px;height:34px;border-radius:50%;background:var(--pink)}
.brand-name{font-size:17px;font-weight:700;color:var(--pink);line-height:1.05;width:90px}
.utility{position:absolute;right:0;top:8px;display:flex;gap:10px;font-size:7.5px;text-transform:uppercase;color:var(--muted)}
.utility span+span::before{content:"|";margin-right:10px;color:#bbb}
.main-nav{position:absolute;right:0;top:44px;display:flex;gap:3px}
.main-nav a{display:block;background:var(--coral);color:#fff;font-size:9px;font-weight:600;text-transform:uppercase;text-decoration:none;padding:8px 14px}
.main-nav a.active{background:var(--coral-dark)}

/* hero */
.hero{top:84px;height:300px;background:var(--hero-bg)}
.hero-copy{position:absolute;left:22px;top:48px;width:340px}
.hero-title{font-size:31px;font-weight:400;color:var(--pink);line-height:1.15}
.hero-text{margin-top:14px;font-size:11px;color:var(--muted);line-height:1.5}
.btn{display:inline-block;background:var(--orange);color:#fff;font-size:8px;font-weight:700;text-transform:uppercase;padding:6px 12px;text-decoration:none}
.hero .btn{margin-top:16px;background:var(--pink);font-size:9px;padding:8px 16px}
.hero-image{position:absolute;left:390px;top:12px;width:406px;height:256px;background:radial-gradient(circle at 40% 45%,#ffffff 0,#dfe7f2 40%,#b8c6da 75%,#9aa9c2 100%)}
.slider-dots{position:absolute;left:22px;bottom:14px;display:flex;gap:5px}
.slider-dots i{width:7px;height:7px;border-radius:50%;background:#c9ccd2}
.slider-dots i:first-child{background:var(--coral)}

/* categories */
.categories{top:394px;height:98px;display:flex;gap:8px}
.cat{flex:1;display:flex;background:var(--green)}
.cat-img{width:84px;height:98px}
.cat-body{flex:1;position:relative;padding:12px 10px;color:#fff}
.cat-name{font-size:13px;font-weight:600;line-height:1.2}
.cat-shop{position:absolute;right:10px;bottom:10px;font-size:8px;font-weight:600}
.img-crystals{background:linear-gradient(160deg,#e9ddf6,#a77fd0)}
.img-books{background:linear-gradient(160deg,#c7e5f7,#5b9bd0)}
.img-pendulums{background:linear-gradient(160deg,#fff6e0,#e0b657)}
.img-reiki{background:linear-gradient(160deg,#bfe6ff,#3c6fc4)}

/* featured */
.section-title{font-size:12px;font-weight:700;text-transform:uppercase;color:var(--ink);padding-bottom:6px;border-bottom:1px solid var(--line)}
.featured{top:506px;height:300px}
.products{display:flex;gap:9px;margin-top:12px}
.product{flex:1;text-align:center}
.product-img{height:122px;border:1px solid var(--line)}
.p1{background:linear-gradient(160deg,#f4f4f6,#b7bdc7)}
.p2{background:radial-gradient(circle,#ffffff 0,#d9dbe0 50%,#9aa0aa 100%)}
.p3{background:radial-gradient(circle,#ffffff 0,#dfe6ef 45%,#9fb2c8 100%)}
.p4{background:radial-gradient(circle,#f3b6cf 0,#9b3c6b 55%,#2b1a33 100%)}
.p5{background:radial-gradient(circle,#ffd7de 0,#f59aa9 50%,#d66c80 100%)}
.product-name{margin-top:10px;font-size:10px;font-weight:600;color:var(--pink)}
.product-text{margin:6px 4px 0;font-size:8px;color:var(--muted);line-height:1.45;height:46px}
.product .btn{margin-top:8px}

/* about + blog */
.lower{top:818px;height:214px}
.about{position:absolute;left:0;top:0;width:546px}
.about p{margin-top:10px;font-size:8.5px;color:var(--muted);line-height:1.6}
.blog{position:absolute;right:0;top:0;width:236px}
.blog-post{display:flex;gap:8px;margin-top:12px}
.blog-img{width:70px;height:70px;flex:none;background:radial-gradient(circle at 50% 40%,#ffe58a 0,#8a4bc9 45%,#1d2a6b 100%)}
.blog-title{font-size:9.5px;font-weight:600;color:var(--pink);line-height:1.3}
.blog-text{margin-top:4px;font-size:8px;color:var(--muted);line-height:1.45}
.read-more{display:block;margin-top:6px;font-size:8px;font-weight:700;color:var(--ink)}

/* footer */
.site-footer{position:absolute;left:0;top:1040px;width:896px;height:160px;background:var(--footer);color:#fff}
.footer-cols{position:absolute;left:44px;top:16px;width:808px;display:flex;gap:14px}
.fcol{width:110px}
.fcol h4{font-size:9.5px;font-weight:700;margin-bottom:6px}
.fcol li{list-style:none;font-size:8px;line-height:1.75}
.social li{display:flex;align-items:center;gap:5px}
.social li::before{content:"";width:9px;height:9px;border-radius:50%;background:#fff;opacity:.85}
.newsletter{margin-left:auto;width:180px}
.newsletter .field{height:20px;background:#fff;margin-top:4px}
.newsletter .btn{margin-top:8px;background:var(--pink);font-size:8px}
.payments{display:flex;gap:4px;margin-top:14px}
.payments i{width:26px;height:16px;background:#fff;border-radius:2px;opacity:.9}
.copyright{position:absolute;left:0;bottom:0;width:896px;height:24px;background:var(--footer-dark);font-size:8px;padding:7px 44px}
</style>
</head>
<body>
<div class="page">

  <header class="wrap site-header">
    <div class="brand"><span class="brand-dot"></span><span class="brand-name">The Velvet Lantern</span></div>
    <div class="utility"><span>Log in</span><span>Register</span><span>My account</span><span>My cart (0)</span><span>Checkout</span></div>
    <nav class="main-nav">
      <a href="#" class="active">Home</a><a href="#">About</a><a href="#">Online store</a><a href="#">Blog</a><a href="#">Contact us</a>
    </nav>
  </header>

  <section class="wrap hero">
    <div class="hero-copy">
      <h1 class="hero-title">Duis aliquam nibh a dui iaculis viverra</h1>
      <p class="hero-text">Aenean a nibh eget turpis vehicula tempus ac sed metus. Vestibulum dolor nulla, ultrices ac tincidunt sed, laoreet nisi est.</p>
      <a href="#" class="btn">View details</a>
    </div>
    <div class="hero-image" role="img" aria-label="Clear quartz crystals arranged on a white surface"></div>
    <div class="slider-dots"><i></i><i></i><i></i><i></i></div>
  </section>

  <section class="wrap categories">
    <div class="cat"><div class="cat-img img-crystals" role="img" aria-label="Purple crystal cluster"></div><div class="cat-body"><div class="cat-name">Crystals</div><span class="cat-shop">Shop Now ›</span></div></div>
    <div class="cat"><div class="cat-img img-books" role="img" aria-label="Stack of books and CDs"></div><div class="cat-body"><div class="cat-name">Books &amp; CDs</div><span class="cat-shop">Shop Now ›</span></div></div>
    <div class="cat"><div class="cat-img img-pendulums" role="img" aria-label="Golden pendulum on a chain"></div><div class="cat-body"><div class="cat-name">Pendulums</div><span class="cat-shop">Shop Now ›</span></div></div>
    <div class="cat"><div class="cat-img img-reiki" role="img" aria-label="Blue glowing energy healing scene"></div><div class="cat-body"><div class="cat-name">Reiki</div><span class="cat-shop">Shop Now ›</span></div></div>
  </section>

  <section class="wrap featured">
    <h2 class="section-title">Featured Products</h2>
    <div class="products">
      <div class="product"><div class="product-img p1" role="img" aria-label="Silver crystal pendulum"></div><div class="product-name">Product name goes here</div><p class="product-text">Aliquam molestie, mi ut imperdiet euismod, dui purus nec.</p><a href="#" class="btn">View details</a></div>
      <div class="product"><div class="product-img p2" role="img" aria-label="Silver pentacle pendant"></div><div class="product-name">Product name goes here</div><p class="product-text">Aliquam molestie, mi ut imperdiet euismod, dui purus nec.</p><a href="#" class="btn">View details</a></div>
      <div class="product"><div class="product-img p3" role="img" aria-label="Meditation music CDs"></div><div class="product-name">Product name goes here</div><p class="product-text">Aliquam molestie, mi ut imperdiet euismod, dui purus nec.</p><a href="#" class="btn">View details</a></div>
      <div class="product"><div class="product-img p4" role="img" aria-label="Faceted pink crystal ball"></div><div class="product-name">Product name goes here</div><p class="product-text">Aliquam molestie, mi ut imperdiet euismod, dui purus nec.</p><a href="#" class="btn">View details</a></div>
      <div class="product"><div class="product-img p5" role="img" aria-label="Rose quartz heart stone"></div><div class="product-name">Product name goes here</div><p class="product-text">Aliquam molestie, mi ut imperdiet euismod, dui purus nec.</p><a href="#" class="btn">View details</a></div>
    </div>
  </section>

  <section class="wrap lower">
    <div class="about">
      <h2 class="section-title">About The Velvet Lantern</h2>
      <p>Aliquam molestie, mi ut imperdiet euismod, dui purus auctor tellus, at interdum lacus lectus at est. Nam accumsan sollicitudin sapien, sit amet adipiscing turpis euismod at. Integer nec neque ac lectus ultrices pellentesque. Morbi mauris sapien, blandit vel tincidunt quis, fringilla vitae nisl. Duis aliquam nibh a dui iaculis viverra et a velit. Vivamus egestas risus in magna varius consequat. Sed semper viverra egestas. Etiam pretium porttitor lectus, vel ornare neque porta volutpat.</p>
      <p>Aenean a nibh eget turpis vehicula tempus ac sed metus. Vestibulum dolor nulla, ultrices ac tincidunt sed, laoreet nisi est. Suspendisse lobortis lorem in nibh cursus laoreet euismod. Etiam risus mauris, vulputate eu pellentesque id, consectetur a neque.</p>
    </div>
    <aside class="blog">
      <h2 class="section-title">Blog Posts</h2>
      <div class="blog-post">
        <div class="blog-img" role="img" aria-label="Colourful chakra energy artwork"></div>
        <div>
          <div class="blog-title">Aliquam molestie, mi ut imperdiet euismod</div>
          <p class="blog-text">Dui purus auctor tellus, at interdum lacus lectus at est. Nam accumsan sapien amet.</p>
          <a href="#" class="read-more">Read more ›</a>
        </div>
      </div>
    </aside>
  </section>

  <footer class="site-footer">
    <div class="footer-cols">
      <div class="fcol"><h4>Company</h4><ul><li>Home</li><li>About</li><li>Blog</li><li>Contact us</li></ul></div>
      <div class="fcol"><h4>Products</h4><ul><li>Crystals</li><li>Books &amp; CDs</li><li>Pendulums</li><li>Reiki</li></ul></div>
      <div class="fcol"><h4>Supports</h4><ul><li>Shipping info</li><li>Returns</li><li>Privacy policy</li><li>Terms of use</li></ul></div>
      <div class="fcol"><h4>Account Info</h4><ul><li>My account</li><li>Order history</li><li>Wish list</li><li>Newsletter</li></ul></div>
      <div class="fcol"><h4>Contact Us</h4><ul class="social"><li>Community</li><li>Updates</li><li>Videos</li><li>Circle</li></ul></div>
      <div class="fcol newsletter"><h4>Newsletter Signup</h4><div class="field"></div><a href="#" class="btn">Subscribe</a>
        <div class="payments"><i></i><i></i><i></i><i></i></div></div>
    </div>
    <div class="copyright">Copyright © 2014 The Velvet Lantern. All Rights Reserved.</div>
  </footer>

</div>
</body>
</html>
```